IT Company requires new Business Card design.

Over the years we have had a few different business card designs. We are now due for new cards across the board for all staff. We felt this would be a good time to start fresh with a new design. Our traditional card simply had our details on the front, and a list of services on the back. We don't particularly need the list of services, we have had cards where the only thing on the rear of the card was our logo.
Feel free to be creative, we would like our tag line "Complete IT Management" to appear at some point, doesn't necessarily have to be with the logo.
I have attached samples and drafts of various previous cards we have used over the years.

```html
<!DOCTYPE html>
<html lang="en">
<head>
<meta charset="utf-8">
<title>Shoreline Networks – Business Card</title>
<link rel="stylesheet" href="https://fonts.googleapis.com/css2?family=Open+Sans:wght@400;600;700;800&display=swap">
<style>
  :root {
    --slate: #5f717d;
    --slate-dark: #566875;
    --paper: #ffffff;
    --ink-soft: #3f4a52;
    --backdrop: #e9ebec;
    --faint: rgba(255,255,255,0.12);
  }
  * { box-sizing: border-box; margin: 0; padding: 0; }
  html, body {
    width: 1034px; height: 1200px; overflow: hidden;
    background: var(--backdrop);
    font-family: "Open Sans", Arial, sans-serif;
  }
  .canvas {
    position: relative; width: 1034px; height: 1200px;
  }
  .card {
    position: absolute; left: 67px; width: 900px; height: 514px;
    box-shadow: 0 6px 18px rgba(0,0,0,0.25);
    overflow: hidden;
  }
  .card--front { top: 65px; background: var(--paper); }
  .card--back { top: 628px; background: var(--slate); }

  /* front */
  .front__brand {
    position: absolute; top: 70px; left: 0; right: 0;
    display: flex; justify-content: center; align-items: center; gap: 26px;
  }
  .brand-square {
    width: 110px; height: 110px; background: var(--slate-dark);
  }
  .brand-name {
    color: var(--slate-dark); font-weight: 800;
    font-size: 58px; line-height: 0.95; letter-spacing: 1px;
    text-transform: uppercase;
  }
  .front__address {
    position: absolute; top: 257px; left: 0; right: 0;
    text-align: center; color: var(--ink-soft); font-size: 21px;
  }
  .front__band {
    position: absolute; left: 0; right: 0; top: 300px; bottom: 0;
    background: var(--slate); color: var(--paper);
  }
  .band__mark {
    position: absolute; left: 625px; top: 28px;
    width: 130px; height: 125px; background: var(--faint);
  }
  .contact { position: absolute; left: 60px; top: 18px; }
  .contact__name { font-size: 27px; font-weight: 700; }
  .contact__role { font-size: 21px; font-weight: 400; }
  .contact__line {
    display: flex; align-items: center; gap: 10px;
    font-size: 21px; margin-top: 6px; height: 29px;
  }
  .contact__line:first-of-type { margin-top: 12px; }
  .icon { width: 18px; height: 18px; fill: var(--paper); flex: none; }
  .gap { width: 8px; }

  /* back */
  .back__brand {
    position: absolute; top: 110px; left: 0; right: 0;
    display: flex; flex-direction: column; align-items: center; gap: 20px;
  }
  .back__brand .brand-square { width: 150px; height: 150px; background: var(--paper); }
  .back__brand .brand-name {
    color: var(--paper); font-size: 54px; text-align: center;
  }
  .tagline {
    position: absolute; top: 448px; left: 0; right: 0;
    text-align: center; color: var(--paper);
    font-size: 23px; letter-spacing: 5px; text-transform: uppercase;
  }
</style>
</head>
<body>
<main class="canvas">
  <section class="card card--front">
    <div class="front__brand">
      <div class="brand-square"></div>
      <div class="brand-name">Shoreline<br>Networks</div>
    </div>
    <p class="front__address">Unit 7 22 Corrie Street, Bayview WA 6150</p>
    <div class="front__band">
      <div class="band__mark"></div>
      <div class="contact">
        <p><span class="contact__name">Mark Ellison,</span> <span class="contact__role">Operation Manager</span></p>
        <p class="contact__line">
          <svg class="icon" viewBox="0 0 20 20"><path d="M4 2l4 0 1.5 4-2.5 1.5a10 10 0 0 0 5.5 5.5L14 10.5l4 1.5v4c0 1-1 2-2 2C8 18 2 12 2 4c0-1 1-2 2-2z"/></svg>
          <span>08 9550 1184</span><span class="gap"></span>
          <svg class="icon" viewBox="0 0 20 20"><path d="M6 1h8a1 1 0 0 1 1 1v16a1 1 0 0 1-1 1H6a1 1 0 0 1-1-1V2a1 1 0 0 1 1-1zm1 2v8h6V3z"/></svg>
          <span>0412 908 671</span>
        </p>
        <p class="contact__line">
          <svg class="icon" viewBox="0 0 20 20"><path d="M5 2h8l2 2v4H5zM2 9h16v7h-3v3H5v-3H2zm5 5v3h6v-3z"/></svg>
          <span>08 9550 1185</span>
        </p>
        <p class="contact__line">
          <svg class="icon" viewBox="0 0 20 20"><path d="M1 4h18v12H1zm2 2v.5l7 5 7-5V6l-7 5z"/></svg>
          <span>mark@shorelinenetworks.com.au</span>
        </p>
        <p class="contact__line">
          <svg class="icon" viewBox="0 0 20 20"><path d="M10 1a9 9 0 1 0 0 18 9 9 0 0 0 0-18zm-1 2.1V9H5.1A7 7 0 0 1 9 3.1zm2 0A7 7 0 0 1 14.9 9H11zM3.1 11H9v5.9A7 7 0 0 1 3.1 11zm7.9 0h5.9A7 7 0 0 1 11 16.9z"/></svg>
          <span>www.shorelinenetworks.com.au</span>
        </p>
      </div>
    </div>
  </section>

  <section class="card card--back">
    <div class="back__brand">
      <div class="brand-square"></div>
      <div class="brand-name">Shoreline Networks</div>
    </div>
    <p class="tagline">Complete IT Management</p>
  </section>
</main>
</body>
</html>
```